Preisliste für Kosmetikinstitut
Zielgruppe
Ich benötige für mein Kosmetikinstitut eine Preisliste für die moderne Frau, aber auch Männer. Das Design sollte mein Logo enthalten. Farben des Designkonzepts einbauen.
A4 quer zum Falten, wie ein Heft, 1. Seite Preisliste mit logo, im Innenteil dann Anwendungen
Aufgabenstellung
Minimalistisch, ästhetisch, modern, edel
Kontaktdaten auf der Rückseite
LB Hautatelier
Lotte Brenner
Lindenhang 17
83671 Waakirchen
EMail: lotte@lb-hautatelier.de
Whatsapp: 0176 284 9017

```html
<!DOCTYPE html>
<html lang="de">
<head>
<meta charset="utf-8">
<title>LB Hautatelier – Preisliste</title>
<link href="https://fonts.googleapis.com/css2?family=Italiana&family=Questrial&display=swap" rel="stylesheet">
<style>
  :root {
    --paper: #f0efed;
    --frame: #f6f6f5;
    --gel-light: #f3f3f2;
    --gel-mid: #e8e8e7;
    --gel-shade: #dededd;
    --sage-ink: #5f6e6d;
  }
  * { margin: 0; padding: 0; box-sizing: border-box; }
  html, body { width: 849px; height: 1200px; overflow: hidden; background: var(--paper); }
  .cover {
    position: relative;
    width: 849px;
    height: 1200px;
    background: var(--paper);
  }
  .cover__frame {
    position: absolute;
    left: 265px;
    top: 0;
    width: 319px;
    height: 619px;
    background: var(--frame);
  }
  .cover__visual {
    position: absolute;
    left: 269px;
    top: 0;
    width: 311px;
    height: 615px;
    background:
      repeating-linear-gradient(155deg,
        rgba(255,255,255,0) 0px,
        rgba(255,255,255,0.55) 38px,
        rgba(255,255,255,0) 70px,
        rgba(210,210,209,0.35) 96px,
        rgba(255,255,255,0) 120px),
      linear-gradient(165deg, var(--gel-light) 0%, var(--gel-mid) 30%, var(--gel-light) 52%, var(--gel-mid) 72%, var(--gel-shade) 100%);
  }
  .cover__brand {
    position: absolute;
    left: 320px;
    top: 266px;
    width: 210px;
    height: 84px;
  }
  .cover__brand-name {
    position: absolute;
    left: 0;
    top: 42px;
    font-family: "Questrial", sans-serif;
    font-size: 19px;
    line-height: 1;
    letter-spacing: 0.02em;
    text-transform: uppercase;
    color: var(--sage-ink);
    white-space: nowrap;
  }
  .cover__brand-mark {
    position: absolute;
    left: 150px;
    top: 0;
    width: 60px;
    height: 60px;
    border: 1.5px solid var(--sage-ink);
    border-radius: 50%;
  }
  .cover__title {
    position: absolute;
    left: 0;
    width: 849px;
    top: 1092px;
    text-align: center;
    font-family: "Italiana", serif;
    font-size: 40px;
    line-height: 1;
    letter-spacing: 0.15em;
    padding-left: 0.15em;
    color: var(--sage-ink);
  }
</style>
</head>
<body>
  <main class="cover">
    <div class="cover__frame"></div>
    <div class="cover__visual" role="img" aria-label="Nahaufnahme von transparentem Pflegegel mit sanften Wellen und kleinen Luftbläschen"></div>
    <div class="cover__brand">
      <span class="cover__brand-mark"></span>
      <span class="cover__brand-name">LB Hautatelier</span>
    </div>
    <h1 class="cover__title">PREISLISTE</h1>
  </main>
</body>
</html>
```